Communication and Marketing agency needs a new presentation card

We are a group of communication and marketing agencies specialized in companies that are in the logistics and industrial sector. The head agency is TELVANO Grupo and the group consists of 4 agencies: TELVANO Media, TELVANO Digital, TELVANO Research and DifundeEnPantalla. We hace 4 offices in Spain (Madrid, Barcelona, Valencia and Murcia). We are looking for a clean and attractive design that transmits our experience, brand presence in the market and knowledge to those who receive the card.It has to maintain the colors of the logo that is attached.
Target Market(s)
logistics and industrial sector
Marketing department
Contact Information for Business Card
Clean and attractive design

```html
<!DOCTYPE html>
<html lang="es">
<head>
<meta charset="utf-8">
<title>TELVANO Grupo – Tarjeta de visita</title>
<link rel="stylesheet" href="https://fonts.googleapis.com/css2?family=Archivo:wght@800&family=Roboto+Condensed:wght@300;400;500&display=swap">
<style>
  :root {
    --page: #ffffff;
    --card: #000000;
    --band-light: #ffffff;
    --band-dark: #1f1f20;
    --brand-red: #b0222b;
    --brand-grey: #58585a;
    --city-grey: #5c5c5e;
    --ink-light: #ffffff;
    --ink-dark: #1a1a1a;
  }
  * { box-sizing: border-box; margin: 0; padding: 0; }
  html, body {
    width: 1200px; height: 1200px; overflow: hidden;
    background: var(--page);
  }
  body { position: relative; font-family: "Roboto Condensed", Arial, sans-serif; }

  .card {
    position: absolute; left: 272px; width: 664px; height: 379px;
    background: var(--card); overflow: hidden;
    box-shadow: 8px 10px 16px rgba(0,0,0,0.22);
  }
  .card--front { top: 171px; }
  .card--back { top: 657px; }

  /* Front */
  .brand-mark {
    position: absolute; right: 128px; top: 48px;
    color: var(--brand-red); font-weight: 500; text-align: right; line-height: 1;
  }
  .brand-mark__name { display: block; font-size: 92px; letter-spacing: 2px; }
  .brand-mark__sub { display: block; font-size: 54px; margin-top: 4px; }

  .agency-band {
    position: absolute; left: 0; top: 221px; width: 100%; height: 58px;
    background: var(--band-light);
  }
  .agency {
    position: absolute; top: 13px; transform: translateX(-50%);
    font-weight: 500; text-align: right; line-height: 1;
  }
  .agency__name { display: block; font-size: 20px; letter-spacing: 0.5px; }
  .agency__sub { display: block; font-size: 14px; margin-top: 2px; }
  .agency--grey { color: var(--brand-grey); }
  .agency--red { color: var(--brand-red); }
  .agency--digital { left: 106px; }
  .agency--media { left: 257px; }
  .agency--research { left: 408px; }
  .agency--screen { left: 556px; top: 19px; font-size: 16px; }

  .office-band {
    position: absolute; left: 0; top: 279px; width: 100%; height: 45px;
    background: var(--band-dark);
    display: flex; align-items: center; justify-content: center; gap: 14px;
    font-family: "Archivo", Arial, sans-serif; font-weight: 800;
    font-size: 20px; color: var(--city-grey); letter-spacing: 0.3px;
  }
  .office-band__dot { font-size: 14px; }

  /* Back */
  .contact {
    position: absolute; right: 60px; top: 50px; text-align: right;
    color: var(--ink-light); font-weight: 300; font-size: 25px; line-height: 32px;
    letter-spacing: -0.3px;
  }
  .contact__social { display: flex; align-items: center; justify-content: flex-end; gap: 9px; }
  .contact__social-dot {
    width: 21px; height: 21px; border-radius: 50%; background: var(--ink-light);
  }
  .contact__web { margin-top: 14px; font-weight: 400; font-size: 25px; }

  .person-band {
    position: absolute; left: 0; top: 222px; width: 100%; height: 101px;
    background: var(--band-light);
    padding: 12px 0 0 59px; font-weight: 300; font-size: 31px; line-height: 38px;
  }
  .person-band__name { color: var(--brand-red); }
  .person-band__role { color: var(--ink-dark); }
</style>
</head>
<body>

<section class="card card--front" aria-label="Anverso de la tarjeta">
  <div class="brand-mark">
    <span class="brand-mark__name">TELVANO</span>
    <span class="brand-mark__sub">Grupo</span>
  </div>

  <div class="agency-band">
    <div class="agency agency--grey agency--digital"><span class="agency__name">TELVANO</span><span class="agency__sub">Digital</span></div>
    <div class="agency agency--red agency--media"><span class="agency__name">TELVANO</span><span class="agency__sub">Media</span></div>
    <div class="agency agency--grey agency--research"><span class="agency__name">TELVANO</span><span class="agency__sub">Research</span></div>
    <div class="agency agency--red agency--screen"><span class="agency__name">DifundeEnPantalla</span></div>
  </div>

  <div class="office-band">
    <span>MADRID</span><span class="office-band__dot">•</span>
    <span>BARCELONA</span><span class="office-band__dot">•</span>
    <span>VALENCIA</span><span class="office-band__dot">•</span>
    <span>MURCIA</span>
  </div>
</section>

<section class="card card--back" aria-label="Reverso de la tarjeta">
  <div class="contact">
    <p>T. 910 000 412 / M. 600 000 718</p>
    <p>lbernal@telvano.es</p>
    <p class="contact__social"><span class="contact__social-dot"></span>lucasbernal</p>
    <p class="contact__web">www.telvano.es</p>
  </div>

  <div class="person-band">
    <p class="person-band__name">Lucas Bernal</p>
    <p class="person-band__role">Director</p>
  </div>
</section>

</body>
</html>
```